Roadside building business signage for a holistic health clinic.

Replace signs as shown in the attached file. They are perforated stickers that go on the windows as shown. Looking for something that has our logo and says the name of the practice with logo (Fernridge Health & Wellness) also boldly says Acupuncture, IV Vitamins, and Holistic Health.
Possibly our phone number as well 318-562-7041
Updates

Please don't use pink except the logo. Earthy, organic tone colors appreciated.

Need of eye catching window signage of a holistic clinic on a brick building. Pink, purple, sage green, white color. Logo is pink on a white background. Please don't overload with too much pink. Words to include are "Fernridge Health and Wellness(name of business)", "Direct Primary Care", " Medical acupuncture", "IV Vitamin Therapy", "fernridgecareclinic.example","318-562-7041".

Target Market(s)

People will see in their cars passing by the building. Busy roadside so need to be visible while passing in fast speed.

Industry/Entity Type

Health & Wellness

Font styles to use
Sans Serif

Colors

Designer to choose colors to be used in the design.

Requirements
Must have
• On sign must have words Holistic Medicine, Medical Acupuncture, Direct Primary Care and IV vitamins.
Nice to have
• Simple, minimalistic, artistic yet has clear message. White, Black, Violet, Pink (logo), Dark green, Sage green.
Should not have
• Bold colors (red, yellow, blue), same tone colors. Blue waves on the current signage (uploaded file) must go.

```html
<!DOCTYPE html>
<html lang="en">
<head>
<meta charset="utf-8">
<title>Fernridge Health &amp; Wellness – Window Signage</title>
<link href="https://fonts.googleapis.com/css2?family=Montserrat:wght@500;600;700&display=swap" rel="stylesheet">
<style>
  :root {
    --canvas: #e3e3e3;
    --forest: #0f4d3e;
    --logo-pink: #e0378a;
    --sage: #8fa58c;
    --sage-light: #dde5da;
    --violet: #6b5088;
    --paper: #ffffff;
    --wash: rgba(190, 207, 184, 0.45);
    --cream: rgba(238, 232, 218, 0.6);
  }
  * { margin: 0; padding: 0; box-sizing: border-box; }
  html, body { width: 800px; height: 1200px; overflow: hidden; }
  body {
    background: var(--canvas);
    font-family: "Montserrat", sans-serif;
    position: relative;
  }
  .sign {
    position: absolute;
    top: 432px;
    width: 337px;
    height: 337px;
    overflow: hidden;
    background:
      radial-gradient(circle at 85% 10%, var(--wash), transparent 45%),
      radial-gradient(circle at 10% 75%, var(--cream), transparent 42%),
      radial-gradient(circle at 60% 55%, rgba(220, 230, 214, 0.4), transparent 45%),
      var(--paper);
  }
  .sign--services { left: 46px; }
  .sign--brand { left: 408px; }

  .brand-mark {
    position: absolute;
    left: 50%;
    transform: translateX(-50%);
    border-radius: 50%;
    background: var(--logo-pink);
  }
  .brand-name {
    position: absolute;
    left: 0; right: 0;
    text-align: center;
    color: var(--forest);
    font-weight: 500;
    line-height: 1;
  }
  .brand-name .tagline { display: block; }

  .sign--services .brand-mark { top: 14px; width: 40px; height: 40px; }
  .sign--services .brand-name { top: 64px; font-size: 24px; letter-spacing: 3px; }
  .sign--services .brand-name .tagline { font-size: 8px; letter-spacing: 4.5px; margin-top: 5px; }

  .services { position: absolute; left: 52px; top: 110px; list-style: none; }
  .service {
    position: relative;
    height: 26px;
    width: 232px;
    margin-bottom: 6px;
    padding-left: 28px;
  }
  .service::before {
    content: "";
    position: absolute;
    left: 18px; top: 0;
    width: 214px; height: 26px;
    background: var(--sage-light);
  }
  .service-dot {
    position: absolute;
    left: 0; top: -1px;
    width: 28px; height: 28px;
    border-radius: 50%;
    background: var(--sage);
    border: 2px solid var(--paper);
    box-shadow: 0 0 0 1px var(--forest);
  }
  .service-label {
    position: relative;
    font-weight: 700;
    font-size: 14.5px;
    line-height: 26px;
    color: var(--forest);
    padding-left: 8px;
    white-space: nowrap;
  }

  .contact-band { position: absolute; left: 0; bottom: 0; width: 337px; height: 92px; }
  .phone-number {
    position: absolute;
    left: 0; right: 0; bottom: 26px;
    text-align: center;
    color: var(--paper);
    font-weight: 700;
    font-size: 22px;
    letter-spacing: 1.5px;
    line-height: 1;
  }
  .website {
    position: absolute;
    left: 0; right: 0; bottom: 9px;
    text-align: center;
    color: var(--sage-light);
    font-weight: 600;
    font-size: 10.5px;
    letter-spacing: 0.5px;
    line-height: 1;
  }

  .sign--brand .brand-mark { top: 92px; width: 74px; height: 74px; }
  .sign--brand .brand-name { top: 186px; font-size: 35px; letter-spacing: 4px; }
  .sign--brand .brand-name .tagline { font-size: 11px; letter-spacing: 6px; margin-top: 8px; }
</style>
</head>
<body>

<section class="sign sign--services">
  <span class="brand-mark" aria-hidden="true"></span>
  <h1 class="brand-name">FERNRIDGE<span class="tagline">HEALTH &amp; WELLNESS</span></h1>

  <ul class="services">
    <li class="service"><span class="service-dot"></span><span class="service-label">Direct Primary Care</span></li>
    <li class="service"><span class="service-dot"></span><span class="service-label">Medical Acupuncture</span></li>
    <li class="service"><span class="service-dot"></span><span class="service-label">IV Vitamin Therapy</span></li>
    <li class="service"><span class="service-dot"></span><span class="service-label">Holistic Medicine</span></li>
  </ul>

  <svg class="contact-band" viewBox="0 0 337 92" aria-hidden="true">
    <path d="M0,52 Q168,-8 337,52 L337,92 L0,92 Z" fill="var(--violet)"/>
    <path d="M0,59 Q168,6 337,59 L337,92 L0,92 Z" fill="var(--forest)"/>
    <circle cx="168" cy="20" r="18" fill="var(--sage)" stroke="var(--paper)" stroke-width="2"/>
    <g transform="translate(168 20) scale(0.78) translate(-169 -10)">
      <path d="M160,2 c1.5,-1 3,-0.5 3.6,1 l1.6,3.6 c0.5,1.2 0,2.3 -1,3 l-1.4,1 c1.2,2.8 3.4,5 6.2,6.3 l1,-1.4 c0.7,-1 1.9,-1.4 3,-0.9 l3.5,1.6 c1.4,0.6 1.9,2.1 1,3.6 l-1.3,2 c-0.9,1.3 -2.5,1.9 -4,1.5 c-7.5,-2 -13.2,-7.8 -15.2,-15.3 c-0.4,-1.5 0.2,-3.1 1.5,-4 Z" fill="var(--paper)"/>
      <path d="M171,2.5 a7,7 0 0 1 6,6 M171,-1.5 a11,11 0 0 1 10,10" fill="none" stroke="var(--paper)" stroke-width="1.4" stroke-linecap="round"/>
    </g>
  </svg>
  <p class="phone-number">318-562-7041</p>
  <p class="website">fernridgecareclinic.example</p>
</section>

<section class="sign sign--brand">
  <span class="brand-mark" aria-hidden="true"></span>
  <h2 class="brand-name">FERNRIDGE<span class="tagline">HEALTH &amp; WELLNESS</span></h2>
</section>

</body>
</html>
```